Every Shelf Set Neatly or ESN Organized needs a business card design. ESN Organized is a professi

We need a business card design that is clean, sharp and conveys a sense of organization. I already have a logo.

Target Market(s)

Families (specifically mothers), small business owners, parents, seniors

Industry/Entity Type

Business

Contact Information for Business Card

My website is www.esnorganized-example.com and my Facebook page is http://www.sociallink-example.com/everyshelfsetneatly. The phone number is 418-552-7094 and I want to be listed as Lorna M. Pelham, Owner

Requirements
Must have
• My logo.

```html
<!DOCTYPE html>
<html lang="en">
<head>
<meta charset="UTF-8">
<title>Every Shelf Set Neatly – Business Card</title>
<link href="https://fonts.googleapis.com/css2?family=Montserrat:wght@400;600&family=Open+Sans:wght@400;600&display=swap" rel="stylesheet">
<style>
  :root {
    --page-bg: #e9e9e6;
    --card-dark: #0d0d0d;
    --card-dark-2: #2a2a2a;
    --card-light: #ffffff;
    --brand-blue: #1f7fd1;
    --brand-blue-deep: #0f63b0;
    --text-light: #ffffff;
    --text-dark: #2b2b2b;
  }
  * { margin: 0; padding: 0; box-sizing: border-box; }
  html, body { width: 1200px; height: 843px; overflow: hidden; }
  body {
    background: var(--page-bg);
    display: flex;
    align-items: center;
    justify-content: center;
    gap: 48px;
    font-family: "Open Sans", sans-serif;
  }
  .card {
    position: relative;
    width: 530px;
    height: 303px;
    border-radius: 4px;
    overflow: hidden;
    box-shadow: 0 10px 26px rgba(0,0,0,0.22);
  }
  .brand {
    display: flex;
    align-items: center;
    gap: 10px;
    font-family: "Montserrat", sans-serif;
    font-weight: 400;
    letter-spacing: 0.01em;
    white-space: nowrap;
  }
  .brand__dot {
    width: 12px; height: 12px;
    border-radius: 50%;
    background: var(--brand-blue);
    flex: none;
  }
  /* Back face */
  .card--back {
    background: var(--card-light);
    display: flex;
    flex-direction: column;
    align-items: center;
    justify-content: center;
    gap: 36px;
  }
  .card--back .brand { font-size: 27px; color: var(--text-dark); }
  .back-web {
    font-family: "Montserrat", sans-serif;
    font-size: 12px;
    letter-spacing: 0.26em;
    color: var(--text-dark);
  }
  /* Front face */
  .card--front {
    background: linear-gradient(160deg, var(--card-dark-2) 0%, var(--card-dark) 55%);
  }
  .accent-panel {
    position: absolute;
    inset: 0;
    background: linear-gradient(135deg, var(--brand-blue) 0%, var(--brand-blue-deep) 100%);
    clip-path: polygon(58% 100%, 100% 100%, 100% 14%, 86% 4%);
  }
  .card--front .brand {
    position: absolute;
    left: 40px; top: 34px;
    font-size: 20px;
    color: var(--text-light);
  }
  .person {
    position: absolute;
    left: 40px; top: 108px;
  }
  .person__name {
    font-family: "Montserrat", sans-serif;
    font-weight: 600;
    font-size: 19px;
    color: var(--brand-blue);
    text-transform: uppercase;
  }
  .person__role {
    font-size: 12px;
    color: var(--text-light);
    text-transform: uppercase;
    margin-top: 4px;
  }
  .contact {
    position: absolute;
    left: 40px; top: 184px;
    list-style: none;
    color: var(--text-light);
    font-size: 13.5px;
  }
  .contact li {
    display: flex;
    align-items: center;
    gap: 9px;
    line-height: 22px;
  }
  .contact__icon { width: 12px; height: 12px; flex: none; }
</style>
</head>
<body>
  <section class="card card--back" aria-label="Card back">
    <div class="brand"><span class="brand__dot"></span>Every Shelf Set Neatly</div>
    <p class="back-web">www.esnorganized-example.com</p>
  </section>

  <section class="card card--front" aria-label="Card front">
    <div class="accent-panel" role="img" aria-label="Large paper clip illustration on blue"></div>
    <div class="brand"><span class="brand__dot"></span>Every Shelf Set Neatly</div>
    <div class="person">
      <p class="person__name">Lorna M. Pelham</p>
      <p class="person__role">Owner</p>
    </div>
    <ul class="contact">
      <li>
        <svg class="contact__icon" viewBox="0 0 24 24" aria-hidden="true"><path fill="#1f7fd1" d="M6.6 10.8a15.1 15.1 0 0 0 6.6 6.6l2.2-2.2a1 1 0 0 1 1-.25 11.4 11.4 0 0 0 3.6.57 1 1 0 0 1 1 1V20a1 1 0 0 1-1 1A17 17 0 0 1 3 4a1 1 0 0 1 1-1h3.5a1 1 0 0 1 1 1c0 1.25.2 2.45.57 3.57a1 1 0 0 1-.25 1z"/></svg>
        418-552-7094
      </li>
      <li>
        <svg class="contact__icon" viewBox="0 0 24 24" aria-hidden="true"><circle cx="12" cy="12" r="10" fill="#1f7fd1"/></svg>
        www.esnorganized-example.com
      </li>
      <li>
        <svg class="contact__icon" viewBox="0 0 24 24" aria-hidden="true"><rect x="2" y="2" width="20" height="20" fill="#1f7fd1"/></svg>
        everyshelfsetneatly
      </li>
    </ul>
  </section>
</body>
</html>
```